KAJU Freightways #ALLKAJU Business Cards & Letterhead

I am looking to business cards designed for our organization. We are currently undergoing a small re-branding that is taking place. Our organization is called KAJU Freightways and we are headquartered in Phoenix, AZ. We primarily provide transportation and logistics services to the Marlow Parcel Bureau who is our largest customer. I would like to see a design that incorporates name, title, contact info, website, and address (this will be different depending on the employee). I would also like to see some color on the business card using our logo colors or a variation. I would like our logo on the back of the business card with the website displayed. The final design should communicate that we are a next generation transportation operate that focuses on being driver-first, customer-centric, innovative, and sustainable.We would also like our #ALLKAJU catch phrase incorporated as well.

Target Market(s)

Transportation & Logistics

Industry/Entity Type

Trucking Company

Contact Information for Business Card

-First and Last Name
-Position Title
-Contact Phone
-Contact Email
-Physical Address

Font styles to use
Serif

Colors

Designer to choose colors to be used in the design.

Requirements
Must have
• -KAJU logo prominently displayed
• -#ALLKAJU catch phrase used
• -Some amount of color, design gradient, etc.
• -Logo on the back with website listed (https://www.kajufreightco.example)

```html
<!DOCTYPE html>
<html lang="en">
<head>
<meta charset="utf-8">
<title>KAJU Freightways Business Card</title>
<link rel="stylesheet" href="https://fonts.googleapis.com/css2?family=Libre+Baskerville:wght@400;700&display=swap">
<style>
  :root {
    --bg: #d9d9d9;
    --card-white: #ffffff;
    --teal-light: #0d6470;
    --teal-dark: #013f4d;
    --green: #7dc242;
    --navy: #0d3345;
    --black-top: #2e2e2e;
    --black-bottom: #1c1c1c;
    --silver: #b9b9b9;
    --white: #ffffff;
  }
  * { margin: 0; padding: 0; box-sizing: border-box; }
  html, body { width: 1200px; height: 960px; overflow: hidden; }
  body {
    background: var(--bg);
    font-family: "Libre Baskerville", Georgia, serif;
    position: relative;
  }
  .card {
    position: absolute;
    left: 250px;
    width: 700px;
    height: 400px;
    border-radius: 26px;
    overflow: hidden;
    box-shadow: 0 10px 30px rgba(0,0,0,0.22);
  }
  .card-back {
    top: 50px;
    background: linear-gradient(160deg, var(--black-top), var(--black-bottom));
  }
  .card-front {
    top: 500px;
    background: var(--card-white);
  }
  .card-art { position: absolute; inset: 0; width: 100%; height: 100%; }

  .logo {
    position: absolute;
    display: flex;
    align-items: center;
    justify-content: center;
    border-radius: 50%;
    font-weight: 700;
    letter-spacing: 1px;
  }
  .card-back .logo {
    left: 255px; top: 80px;
    width: 190px; height: 190px;
    border: 4px solid var(--silver);
    color: var(--silver);
    font-size: 44px;
  }
  .back-tagline {
    position: absolute;
    left: 0; right: 0;
    top: 290px;
    text-align: center;
    color: var(--silver);
    font-size: 16px;
    font-weight: 700;
    letter-spacing: 3px;
  }
  .back-website {
    position: absolute;
    left: 0; right: 0;
    bottom: 30px;
    text-align: center;
    color: var(--silver);
    font-size: 13px;
    letter-spacing: 1px;
  }
  .card-front .logo {
    left: 60px; top: 85px;
    width: 230px; height: 230px;
    border: 6px solid var(--green);
    color: var(--navy);
    font-size: 52px;
  }

  .contact {
    position: absolute;
    right: 34px;
    top: 112px;
    text-align: right;
    color: var(--white);
  }
  .contact-name {
    color: var(--green);
    font-size: 21px;
    font-weight: 400;
    letter-spacing: 0.5px;
  }
  .contact-title {
    font-size: 13px;
    font-weight: 700;
    margin-top: 4px;
  }
  .contact-address {
    font-size: 12.5px;
    line-height: 1.55;
    margin-top: 16px;
  }
  .contact-list {
    list-style: none;
    font-size: 12.5px;
    line-height: 1.7;
    margin-top: 8px;
  }
  .contact-list li {
    display: flex;
    align-items: center;
    justify-content: flex-end;
    gap: 7px;
  }
  .contact-icon { width: 13px; height: 13px; flex: none; }
</style>
</head>
<body>

  <section class="card card-back" aria-label="Business card back">
    <div class="logo">KAJU</div>
    <p class="back-tagline">#ALLKAJU</p>
    <p class="back-website">www.kajufreightco.example</p>
  </section>

  <section class="card card-front" aria-label="Business card front">
    <svg class="card-art" viewBox="0 0 700 400" aria-hidden="true">
      <defs>
        <linearGradient id="tealPanel" x1="0" y1="0" x2="1" y2="1">
          <stop offset="0" stop-color="#0d6470"/>
          <stop offset="1" stop-color="#013f4d"/>
        </linearGradient>
      </defs>
      <path d="M 392 0 C 492 130, 478 300, 322 400 L 700 400 L 700 0 Z" fill="url(#tealPanel)"/>
      <path d="M 376 8 C 472 130, 462 300, 296 398 C 440 300, 452 140, 376 8 Z" fill="#7dc242"/>
    </svg>

    <div class="logo">KAJU</div>

    <div class="contact">
      <p class="contact-name">DANA REYES</p>
      <p class="contact-title">President</p>
      <p class="contact-address">412 Cedar Hollow Road<br>Flagstaff, Arizona 86001</p>
      <ul class="contact-list">
        <li>555-014-2278
          <svg class="contact-icon" viewBox="0 0 24 24"><path fill="#7dc242" d="M6.6 10.8a15 15 0 0 0 6.6 6.6l2.2-2.2c.3-.3.7-.4 1-.2 1.1.4 2.3.6 3.6.6.6 0 1 .4 1 1V20c0 .6-.4 1-1 1A17 17 0 0 1 3 4c0-.6.4-1 1-1h3.5c.6 0 1 .4 1 1 0 1.3.2 2.5.6 3.6.1.3 0 .7-.2 1z"/></svg>
        </li>
        <li>dana@kajufreightco.example
          <svg class="contact-icon" viewBox="0 0 24 24"><path fill="#7dc242" d="M3 5h18v14H3z"/><path fill="none" stroke="#013f4d" stroke-width="2" d="M3 6l9 7 9-7"/></svg>
        </li>
        <li>www.kajufreightco.example
          <svg class="contact-icon" viewBox="0 0 24 24"><circle cx="12" cy="12" r="10" fill="#7dc242"/><path fill="#013f4d" d="M9 8l7 4-7 4z"/></svg>
        </li>
      </ul>
    </div>
  </section>

</body>
</html>
```